32 x 24 Swinging Real Estate Yard Sign

We are looking to design a new sign for our business to focus on the remodeling of homes to sell. We are looking to have a yard sign that gets peoples attention and is informational. The headline will be "The Secret to Top Dollar? Remodel First.". We remodel homes for sellers with no up front cost, as they simply pay at closing. This link has more info, https://bramblecresthomes.com/Remodel
The message we want to convey to those seeing the sign is we are a one stop shop, who can renovate your home and sell it for no stress. We are licensed real estate agents and licensed contractors.
Both of these license numbers and info need to be on the design:
CADRE #02794613
Contractors License #1178524
Email: info@bramblecresthomes.com
Phone: (408)614-2907
I'll attach a sample sign we have for our agents normally as well as all brand art work.
• Pantone Colors
o #172A41
Dark blue
o #4381B1
Medium blue
o #6FA6CC
Light blue
Target Market(s)
Residential Real Estate Sellers
Industry/Entity Type
Real Estate
Colors
Designer to choose colors to be used in the design.

```html
<!DOCTYPE html>
<html lang="en">
<head>
<meta charset="utf-8">
<title>Bramblecrest Homes – Remodel First Yard Sign</title>
<link rel="stylesheet" href="https://fonts.googleapis.com/css2?family=League+Spartan:wght@600;700&family=Poppins:wght@500;600&family=Roboto:wght@500&display=swap">
<style>
  :root {
    --stage: #adadad;
    --navy: #172a41;
    --band: #3a6890;
    --accent: #2e8fd8;
    --brand-light: #6fa6cc;
    --white: #ffffff;
  }
  html, body {
    margin: 0;
    width: 981px;
    height: 1200px;
    overflow: hidden;
    background: var(--stage);
  }
  .sign {
    position: absolute;
    left: 120px;
    top: 106px;
    width: 741px;
    height: 988px;
    background: var(--navy);
    overflow: hidden;
    font-family: "League Spartan", sans-serif;
    color: var(--white);
  }
  .row {
    position: absolute;
    left: 0;
    width: 100%;
    display: flex;
    align-items: center;
    justify-content: center;
    line-height: 1;
    white-space: nowrap;
  }
  .brand {
    top: 86px;
    height: 60px;
    gap: 16px;
  }
  .brand-dot {
    width: 26px;
    height: 26px;
    border-radius: 50%;
    background: var(--brand-light);
  }
  .brand-name {
    font-weight: 600;
    font-size: 44px;
    letter-spacing: 1px;
    padding-top: 6px;
  }
  .lead {
    top: 230px;
    height: 50px;
    font-weight: 700;
    font-size: 54px;
    padding-top: 6px;
  }
  .question {
    top: 285px;
    height: 58px;
    font-weight: 700;
    font-size: 68px;
    color: var(--accent);
    padding-top: 8px;
  }
  .headline {
    top: 366px;
    height: 96px;
    font-weight: 600;
    font-size: 124px;
    letter-spacing: -1px;
    padding-top: 14px;
  }
  .headline-accent {
    top: 474px;
    height: 96px;
    font-weight: 600;
    font-size: 124px;
    color: var(--accent);
    padding-top: 14px;
  }
  .email {
    top: 608px;
    height: 52px;
    font-family: "Roboto", sans-serif;
    font-weight: 500;
    font-size: 44px;
  }
  .phone-band {
    top: 692px;
    height: 109px;
    background: var(--band);
    font-weight: 700;
    font-size: 98px;
    letter-spacing: -1px;
    padding-top: 10px;
    box-sizing: border-box;
  }
  .licence {
    position: absolute;
    height: 49px;
    display: flex;
    border-radius: 12px;
    background: var(--band);
    font-family: "Poppins", sans-serif;
    font-size: 27px;
    line-height: 1;
    white-space: nowrap;
  }
  .licence-label {
    display: flex;
    align-items: center;
    justify-content: center;
    background: var(--white);
    color: var(--navy);
    border-radius: 12px;
    font-weight: 500;
  }
  .licence-number {
    flex: 1;
    display: flex;
    align-items: center;
    justify-content: center;
    font-weight: 600;
    color: var(--white);
  }
  .licence--cadre { left: 193px; top: 828px; width: 355px; }
  .licence--cadre .licence-label { width: 152px; }
  .licence--contractor { left: 100px; top: 890px; width: 540px; }
  .licence--contractor .licence-label { width: 356px; }
</style>
</head>
<body>
  <main class="sign">
    <div class="row brand">
      <span class="brand-dot"></span>
      <span class="brand-name">BRAMBLECREST HOMES</span>
    </div>

    <h1 class="row lead" style="margin:0">THE SECRET TO</h1>
    <p class="row question" style="margin:0">TOP DOLLAR?</p>
    <p class="row headline" style="margin:0">REMODEL</p>
    <p class="row headline-accent" style="margin:0">FIRST</p>

    <p class="row email" style="margin:0">info@bramblecresthomes.com</p>

    <p class="row phone-band" style="margin:0">(408)614-2907</p>

    <div class="licence licence--cadre">
      <span class="licence-label">CADRE</span>
      <span class="licence-number">#02794613</span>
    </div>
    <div class="licence licence--contractor">
      <span class="licence-label">Contractors License</span>
      <span class="licence-number">#1178524</span>
    </div>
  </main>
</body>
</html>
```